Brivolt Technologies business card design

We need a business card designed with our new logo. it would be great if the card could communicate it is a technology based company.

Target Market(s)

system integrators

Industry/Entity Type

technology, IOT

Contact Information for Business Card

Name, designation, Address, telephone number, email address

Requirements
Must have
• logo and company name
Nice to have
• something to do with technology

```html
<!DOCTYPE html>
<html lang="en">
<head>
<meta charset="UTF-8">
<title>Brivolt Technologies – Business Card</title>
<link rel="stylesheet" href="https://fonts.googleapis.com/css2?family=Quicksand:wght@400;600;700&display=swap">
<style>
  :root {
    --page: #ffffff;
    --card-dark: #212121;
    --card-mid: #2b2b2b;
    --card-light: #3a3a3a;
    --accent: #f7931e;
    --light: #f2f2f2;
  }
  * { margin: 0; padding: 0; box-sizing: border-box; }
  html, body {
    width: 1200px;
    height: 1200px;
    overflow: hidden;
    background: var(--page);
    font-family: "Quicksand", sans-serif;
  }
  .card {
    position: absolute;
    left: 187px;
    width: 824px;
    height: 494px;
    background: linear-gradient(160deg, var(--card-mid) 0%, var(--card-dark) 40%, var(--card-light) 100%);
    box-shadow: 0 6px 22px rgba(0, 0, 0, 0.22);
    overflow: hidden;
  }
  .card--front { top: 129px; }
  .card--back { top: 634px; }

  .brand {
    position: absolute;
    display: flex;
    align-items: center;
    color: var(--light);
    font-weight: 700;
  }
  .brand__square {
    flex: none;
    background: var(--accent);
  }
  .brand__name {
    display: flex;
    flex-direction: column;
    line-height: 1;
  }
  .brand__word { letter-spacing: 0.02em; }
  .brand__sub { letter-spacing: 0.42em; }

  .card--front .brand {
    left: 174px;
    top: 178px;
    gap: 26px;
  }
  .card--front .brand__square { width: 70px; height: 70px; }
  .card--front .brand__word { font-size: 68px; }
  .card--front .brand__sub { font-size: 22px; margin-top: 10px; }

  .card--back .brand {
    left: 78px;
    top: 72px;
    gap: 16px;
  }
  .card--back .brand__square { width: 42px; height: 42px; }
  .card--back .brand__word { font-size: 41px; }
  .card--back .brand__sub { font-size: 13px; margin-top: 7px; }

  .contact-list {
    position: absolute;
    left: 386px;
    top: 196px;
    list-style: none;
  }
  .contact-list__item {
    display: flex;
    align-items: center;
    height: 48.5px;
    color: var(--accent);
    font-size: 30px;
    font-weight: 400;
    letter-spacing: -0.01em;
  }
  .contact-list__icon {
    width: 42px;
    height: 42px;
    margin-right: 10px;
    flex: none;
  }
</style>
</head>
<body>

<section class="card card--front" aria-label="Card front">
  <div class="brand">
    <span class="brand__square"></span>
    <div class="brand__name">
      <span class="brand__word">BRIVOLT</span>
      <span class="brand__sub">TECHNOLOGIES</span>
    </div>
  </div>
</section>

<section class="card card--back" aria-label="Card back">
  <div class="brand">
    <span class="brand__square"></span>
    <div class="brand__name">
      <span class="brand__word">BRIVOLT</span>
      <span class="brand__sub">TECHNOLOGIES</span>
    </div>
  </div>

  <ul class="contact-list">
    <li class="contact-list__item">
      <svg class="contact-list__icon" viewBox="0 0 42 42" aria-hidden="true">
        <path d="M21 3a15 15 0 0 0-15 15c0 9 15 23 15 23s15-14 15-23A15 15 0 0 0 21 3z" fill="#f7931e"/>
        <circle cx="21" cy="17" r="6" fill="#2a2a2a"/>
      </svg>
      harborview27lane
    </li>
    <li class="contact-list__item">
      <svg class="contact-list__icon" viewBox="0 0 42 42" aria-hidden="true">
        <circle cx="21" cy="21" r="19" fill="#f7931e"/>
        <ellipse cx="21" cy="21" rx="7" ry="18" fill="none" stroke="#2a2a2a" stroke-width="3"/>
        <line x1="2" y1="21" x2="40" y2="21" stroke="#2a2a2a" stroke-width="3"/>
      </svg>
      www.brivoltlink.com
    </li>
    <li class="contact-list__item">
      <svg class="contact-list__icon" viewBox="0 0 42 42" aria-hidden="true">
        <rect x="3" y="7" width="36" height="28" rx="3" fill="none" stroke="#f7931e" stroke-width="3"/>
        <path d="M5 9h32L24 23a4 4 0 0 1-6 0z" fill="#f7931e"/>
      </svg>
      brivoltmail.com
    </li>
    <li class="contact-list__item">
      <svg class="contact-list__icon" viewBox="0 0 42 42" aria-hidden="true">
        <path d="M11 5c3-1 5 4 5 6s-3 3-3 5 5 9 9 10 3-3 5-3 6 2 6 5-3 4-6 4C18 32 8 21 8 12c0-3 1-6 3-7z" fill="#f7931e"/>
      </svg>
      0427681935
    </li>
  </ul>
</section>

</body>
</html>
```